BOLD & MINIMALIST DESIGN NEEDED

We want a very bold but minimalistic business card design that is impactful and utilizes both sides of the business card. Our current logo is included for your use.

We want bold fonts and good use of negative space. We don't want the logo to overpower the design.

Target Market(s)

Professionals who are building new commercial buildings.

Industry/Entity Type

Construction

Contact Information for Business Card

Name, Title, email, office phone, cell phone, website

Font styles to use
Serif
Sans Serif

Requirements
Must have
• Bold design!

```html
<!DOCTYPE html>
<html lang="en">
<head>
<meta charset="utf-8">
<title>Ridgemont Build – Business Card</title>
<link href="https://fonts.googleapis.com/css2?family=Montserrat:wght@300;400;700;800&display=swap" rel="stylesheet">
<style>
  :root {
    --backdrop: #d3d3d3;
    --card: #f2f2f0;
    --ink: #111111;
    --green: #5a9a2c;
    --grey: #8a8a8a;
    --rule: #d9d9d6;
  }
  * { box-sizing: border-box; margin: 0; padding: 0; }
  html, body {
    width: 1200px; height: 1051px; overflow: hidden;
    background: var(--backdrop);
    font-family: 'Montserrat', sans-serif;
  }
  .sheet {
    width: 1200px; height: 1051px;
    display: flex; flex-direction: column; align-items: center; justify-content: center;
    gap: 60px;
  }
  .card {
    width: 660px; height: 377px;
    background: var(--card);
    box-shadow: 0 14px 30px rgba(0,0,0,0.16);
    position: relative;
  }
  .brand {
    display: flex; align-items: center; gap: 14px;
    color: var(--ink); font-weight: 800; letter-spacing: 0.02em;
    text-transform: uppercase; white-space: nowrap;
  }
  .brand__mark { background: var(--green); flex: none; }

  .card--front { display: flex; align-items: center; justify-content: center; }
  .card--front .brand { font-size: 44px; }
  .card--front .brand__mark { width: 30px; height: 30px; }

  .card--contact .brand {
    position: absolute; left: 50%; top: 70px; transform: translateX(-38%);
    font-size: 30px;
  }
  .card--contact .brand__mark { width: 20px; height: 20px; }

  .holder {
    position: absolute; left: 56px; top: 190px; text-align: right; width: 230px;
  }
  .holder__name { color: var(--green); font-weight: 700; font-size: 23px; text-transform: uppercase; }
  .holder__title { color: var(--grey); font-weight: 400; font-size: 15px; margin-top: 6px; }

  .divider {
    position: absolute; left: 318px; top: 190px; width: 1px; height: 120px; background: var(--rule);
  }
  .contact {
    position: absolute; left: 346px; top: 196px; list-style: none;
    color: var(--grey); font-weight: 300; font-size: 15px;
  }
  .contact li { display: flex; align-items: center; gap: 10px; height: 27px; }
  .contact svg { width: 14px; height: 14px; fill: var(--green); flex: none; }
</style>
</head>
<body>
<main class="sheet">
  <section class="card card--front" aria-label="Card front">
    <div class="brand"><span class="brand__mark"></span>Ridgemont Build</div>
  </section>

  <section class="card card--contact" aria-label="Card back">
    <div class="brand"><span class="brand__mark"></span>Ridgemont Build</div>

    <div class="holder">
      <p class="holder__name">Marcus Adler</p>
      <p class="holder__title">President</p>
    </div>

    <div class="divider"></div>

    <ul class="contact">
      <li>
        <svg viewBox="0 0 24 24" aria-hidden="true"><path d="M6.6 10.8a15.1 15.1 0 0 0 6.6 6.6l2.2-2.2a1 1 0 0 1 1-.25 11.4 11.4 0 0 0 3.6.57 1 1 0 0 1 1 1V20a1 1 0 0 1-1 1A17 17 0 0 1 3 4a1 1 0 0 1 1-1h3.5a1 1 0 0 1 1 1c0 1.25.2 2.45.57 3.57a1 1 0 0 1-.25 1z"/></svg>
        555-014-2200
      </li>
      <li>
        <svg viewBox="0 0 24 24" aria-hidden="true"><path d="M7 1h10a2 2 0 0 1 2 2v18a2 2 0 0 1-2 2H7a2 2 0 0 1-2-2V3a2 2 0 0 1 2-2zm0 3v14h10V4zm5 15.5a1 1 0 1 0 0 2 1 1 0 0 0 0-2z"/></svg>
        555-014-2201
      </li>
      <li>
        <svg viewBox="0 0 24 24" aria-hidden="true"><path d="M2 5h20v14H2zm2 2v.5l8 5 8-5V7zm0 2.8V17h16V9.8l-8 5z"/></svg>
        m.adler@ridgemont-db.com
      </li>
      <li>
        <svg viewBox="0 0 24 24" aria-hidden="true"><path d="M12 2a10 10 0 1 0 0 20 10 10 0 0 0 0-20zm6.9 6h-3a15 15 0 0 0-1.4-3.9A8 8 0 0 1 18.9 8zM12 4c.8 1.2 1.5 2.5 1.9 4h-3.8c.4-1.5 1.1-2.8 1.9-4zM4.3 14a8 8 0 0 1 0-4h3.4a16 16 0 0 0 0 4zm.8 2h3a15 15 0 0 0 1.4 3.9A8 8 0 0 1 5.1 16zm3-8h-3a8 8 0 0 1 4.4-3.9A15 15 0 0 0 8.1 8zM12 20c-.8-1.2-1.5-2.5-1.9-4h3.8c-.4 1.5-1.1 2.8-1.9 4zm2.3-6H9.7a14 14 0 0 1 0-4h4.6a14 14 0 0 1 0 4zm.2 5.9a15 15 0 0 0 1.4-3.9h3a8 8 0 0 1-4.4 3.9zm1.8-5.9a16 16 0 0 0 0-4h3.4a8 8 0 0 1 0 4z"/></svg>
        www.ridgemont-db.com
      </li>
    </ul>
  </section>
</main>
</body>
</html>
```